Calm Nest

I currently have a squarespace website www.bodysensepillow.comI want a complete design change but I want you to use the current information on the site.
Updates

We will be making a decision this week. Thank You.

```html
<!DOCTYPE html>
<html lang="en">
<head>
<meta charset="utf-8">
<title>Calm Nest</title>
<link href="https://fonts.googleapis.com/css2?family=Montserrat:wght@400;500;600;700&display=swap" rel="stylesheet">
<style>
:root{
  --charcoal:#333333;
  --charcoal-deep:#2b2b2b;
  --night:#1f1f1f;
  --black:#0d0d0d;
  --white:#ffffff;
  --ink:#3a3a3a;
  --muted:#555555;
  --line:#bdbdbd;
}
*{margin:0;padding:0;box-sizing:border-box}
html,body{width:1200px;height:2990px;overflow:hidden}
body{font-family:'Montserrat',sans-serif;color:var(--ink);background:var(--white);position:relative}
.abs{position:absolute}

/* header */
.site-header{left:0;top:0;width:1200px;height:114px;background:var(--charcoal)}
.brand{left:77px;top:38px;font-size:31px;font-weight:700;color:var(--white);letter-spacing:.5px}
.nav{top:49px;font-size:13.5px;color:#e6e6e6;letter-spacing:.6px}
.nav-active::before{content:"";position:absolute;left:0;top:-8px;width:18px;height:1px;background:var(--white)}

/* hero */
.hero-photo{left:0;top:114px;width:1200px;height:552px;background:linear-gradient(100deg,#b9b2ab 0%,#e2dcd6 30%,#f3f1ef 60%,#fbfbfb 100%)}
.hero-badge{left:711px;top:213px;width:354px;height:354px;border-radius:50%;background:var(--charcoal);color:var(--white);display:flex;align-items:center;justify-content:center;text-align:center;font-size:23px;font-weight:700;line-height:38px;letter-spacing:.5px;padding-bottom:12px}
.hero-arrow{left:1012px;top:462px;width:60px;height:60px;border-radius:50%;background:var(--black);display:flex;align-items:center;justify-content:center}

/* about */
.about-frame{left:275px;top:760px;width:291px;height:310px}
.about-photo{left:77px;top:781px;width:468px;height:396px;background:linear-gradient(160deg,#d9d7d5 0%,#a9a8ab 40%,#eeeeee 100%)}
.about-title{left:653px;top:795px;font-size:38px;font-weight:700;color:var(--charcoal);letter-spacing:.5px}
.about-text{left:653px;width:470px;font-size:12.5px;line-height:25px;color:var(--muted)}
.btn-outline{left:656px;top:1069px;width:186px;height:51px;border:1.5px solid var(--charcoal);border-radius:3px;display:flex;align-items:center;justify-content:center;font-size:16px;font-weight:700;color:var(--charcoal);letter-spacing:.4px}

/* categories */
.range{left:0;top:1281px;width:1200px;height:583px;background:var(--charcoal)}
.range-title{left:0;top:1350px;width:1200px;text-align:center;font-size:39px;font-weight:700;color:var(--white);letter-spacing:.5px}
.range-sub{left:0;top:1415px;width:1200px;text-align:center;font-size:17.5px;color:var(--white)}
.card{top:1486px;width:323px;height:291px;background:var(--white)}
.card-photo{width:323px;height:218px}
.card-label{position:absolute;left:24px;top:244px;font-size:19.5px;color:var(--ink)}
.card-arrow{position:absolute;right:22px;top:238px}

/* reviews */
.reviews{left:0;top:1864px;width:1200px;height:522px;background:radial-gradient(ellipse at 30% 50%,#2e2e2e 0%,#1c1c1c 60%,#141414 100%)}
.reviews-title{left:0;top:1914px;width:1200px;text-align:center;font-size:38px;font-weight:700;color:var(--white)}
.review-box{left:267px;top:2032px;width:666px;height:250px;background:rgba(255,255,255,.12)}
.quote-badge{left:558px;top:1989px;width:84px;height:84px;border-radius:50%;background:var(--white);display:flex;align-items:center;justify-content:center}
.client{left:0;top:2113px;width:1200px;text-align:center;font-size:19px;font-weight:500;color:var(--white)}
.review-text{left:320px;top:2154px;width:560px;text-align:center;font-size:13px;line-height:25.5px;color:#eeeeee}
.dot{top:2310px;width:12px;height:12px;border-radius:50%;border:1.5px solid var(--white)}
.dot.on{background:var(--white)}

/* contact */
.contact-title{left:0;top:2436px;width:1200px;text-align:center;font-size:38px;font-weight:700;color:var(--charcoal)}
.field{border:1px solid var(--line);border-radius:2px;font-size:13.5px;color:#777;padding:0 17px;display:flex;align-items:center}
.field.tall{align-items:flex-start;padding-top:18px}
.btn-solid{left:516px;top:2678px;width:168px;height:52px;background:var(--charcoal);border-radius:3px;color:var(--white);font-size:16.5px;font-weight:700;display:flex;align-items:center;justify-content:center;letter-spacing:.4px}

/* footer */
.footer{left:0;top:2812px;width:1200px;height:106px;background:var(--charcoal)}
.divider{top:2812px;width:1px;height:106px;background:#4a4a4a}
.foot-text{font-size:13px;line-height:25px;color:var(--white)}
.legal{left:0;top:2918px;width:1200px;height:72px;background:var(--charcoal-deep);color:#e6e6e6;font-size:13px;display:flex;align-items:center;justify-content:center}
</style>
</head>
<body>

<header class="abs site-header" aria-label="Site header"></header>
<div class="abs brand">CALM NEST</div>
<nav>
  <span class="abs nav nav-active" style="left:559px">HOME</span>
  <span class="abs nav" style="left:630px">COMPANY</span>
  <span class="abs nav" style="left:728px">PILLOWS</span>
  <span class="abs nav" style="left:820px">SHEETS</span>
  <span class="abs nav" style="left:903px">CONTACT</span>
  <span class="abs nav" style="left:999px">PRODUCTS</span>
  <svg class="abs" style="left:1103px;top:47px" width="20" height="20" viewBox="0 0 20 20" fill="none" stroke="#fff" stroke-width="2"><circle cx="8.5" cy="8.5" r="6.5"/><line x1="13.5" y1="13.5" x2="18.5" y2="18.5"/></svg>
</nav>

<section>
  <div class="abs hero-photo" role="img" aria-label="Photo of a smiling woman resting on white pillows in a bright bedroom"></div>
  <div class="abs hero-badge">HELPING PEOPLE<br>SLEEP BETTER IS THE<br>MOST IMPORTANT<br>THING THAT WE DO.</div>
  <div class="abs hero-arrow">
    <svg width="28" height="22" viewBox="0 0 28 22" fill="none" stroke="#fff" stroke-width="2.2" stroke-linecap="round" stroke-linejoin="round"><line x1="2" y1="11" x2="25" y2="11"/><polyline points="16,2 25,11 16,20"/></svg>
  </div>
</section>

<section>
  <svg class="abs about-frame" viewBox="0 0 291 310" aria-hidden="true"><polygon points="0,0 291,0 291,310 270,292 270,21 21,21" fill="#333"/></svg>
  <div class="abs about-photo" role="img" aria-label="Photo of a made bed with grey and white patterned pillows and a grey throw"></div>
  <h2 class="abs about-title">ABOUT US</h2>
  <p class="abs about-text" style="top:854px">Calm Nest believes that sleep is the most important part of your life. We created Calm Nest because better sleep makes for a better life. We carry a variety of speciality sleep products that are made with the finest materials available.</p>
  <p class="abs about-text" style="top:968px">We believe that having the correct pillow is essential to achieving the best night of sleep.&nbsp; Pillows play a vital role in supporting the intricate structures of the head, neck, shoulders, hips, and spine.</p>
  <div class="abs btn-outline">KNOW MORE</div>
</section>

<section>
  <div class="abs range"></div>
  <h2 class="abs range-title">LIVE WELL, SLEEP WELL.</h2>
  <p class="abs range-sub">We custom design, private label and manufacture the highest grade sleep products in the industry at value prices.</p>

  <div class="abs card" style="left:77px">
    <div class="card-photo" role="img" aria-label="Photo of a woman lying in a white bed" style="background:linear-gradient(135deg,#aab5b1,#e9ecee 60%,#cfd3d6)"></div>
    <span class="card-label">COMPANY</span>
    <svg class="card-arrow" width="38" height="38" viewBox="0 0 38 38"><circle cx="19" cy="19" r="18" fill="#333"/><path d="M10 19h16M19 11l8 8-8 8" stroke="#fff" stroke-width="3.4" fill="none" stroke-linecap="round" stroke-linejoin="round"/></svg>
  </div>
  <div class="abs card" style="left:439px">
    <div class="card-photo" role="img" aria-label="Photo of blue textured pillows on a striped bed" style="background:linear-gradient(135deg,#8a7a66,#3fb2d8 35%,#5cc0e0 60%,#b8b4aa)"></div>
    <span class="card-label">PILLOWS</span>
    <svg class="card-arrow" width="38" height="38" viewBox="0 0 38 38"><circle cx="19" cy="19" r="18" fill="#333"/><path d="M10 19h16M19 11l8 8-8 8" stroke="#fff" stroke-width="3.4" fill="none" stroke-linecap="round" stroke-linejoin="round"/></svg>
  </div>
  <div class="abs card" style="left:800px">
    <div class="card-photo" role="img" aria-label="Photo of a bed with striped sheets and a breakfast tray" style="background:linear-gradient(160deg,#6e6258,#c9c8c6 35%,#e4e4e4 70%,#a7a6a4)"></div>
    <span class="card-label">SHEETS</span>
    <svg class="card-arrow" width="38" height="38" viewBox="0 0 38 38"><circle cx="19" cy="19" r="18" fill="#333"/><path d="M10 19h16M19 11l8 8-8 8" stroke="#fff" stroke-width="3.4" fill="none" stroke-linecap="round" stroke-linejoin="round"/></svg>
  </div>
</section>

<section>
  <div class="abs reviews" role="img" aria-label="Dark photo of rumpled bed linen"></div>
  <h2 class="abs reviews-title">REVIEWS</h2>
  <div class="abs review-box"></div>
  <div class="abs quote-badge">
    <svg width="38" height="28" viewBox="0 0 38 28" fill="#333"><path d="M2 28V16C2 7 7 2 15 1v6c-4 1-6 4-6 8h6v13z"/><path d="M21 28V16c0-9 5-14 13-15v6c-4 1-6 4-6 8h6v13z"/></svg>
  </div>
  <div class="abs client">– Client Name</div>
  <p class="abs review-text">Lorem Ipsum is simply dummy text of the printing and typesetting industry. Lorem Ipsum has been the industry's standard dummy text ever since the 1500s, when an unknown printer took a galley of type and scrambled.</p>
  <span class="abs dot on" style="left:568px"></span>
  <span class="abs dot" style="left:586px"></span>
  <span class="abs dot" style="left:603px"></span>
  <span class="abs dot" style="left:621px"></span>
</section>

<section>
  <h2 class="abs contact-title">GET IN TOUCH</h2>
  <div class="abs field" style="left:215px;top:2507px;width:249px;height:45px">Name</div>
  <div class="abs field" style="left:475px;top:2507px;width:250px;height:45px">Email</div>
  <div class="abs field" style="left:736px;top:2507px;width:249px;height:45px">Phone</div>
  <div class="abs field tall" style="left:215px;top:2564px;width:770px;height:103px">Message</div>
  <div class="abs btn-solid">SEND NOW</div>
</section>

<footer>
  <div class="abs footer"></div>
  <span class="abs divider" style="left:420px"></span>
  <span class="abs divider" style="left:782px"></span>

  <svg class="abs" style="left:125px;top:2853px" width="18" height="24" viewBox="0 0 18 24"><path d="M9 0C4 0 0 4 0 9c0 6.5 9 15 9 15s9-8.5 9-15C18 4 14 0 9 0z" fill="#fff"/><circle cx="9" cy="9" r="3.5" fill="#333"/></svg>
  <p class="abs foot-text" style="left:161px;top:2841px">Lorem Ipsum is simply dummy<br>text of the printing.</p>

  <svg class="abs" style="left:533px;top:2853px" width="22" height="22" viewBox="0 0 24 24" fill="#fff"><path d="M6.6 10.8c1.4 2.8 3.8 5.1 6.6 6.6l2.2-2.2c.3-.3.7-.4 1-.2 1.1.4 2.3.6 3.6.6.6 0 1 .4 1 1V20c0 .6-.4 1-1 1C10.6 21 3 13.4 3 4c0-.6.4-1 1-1h3.5c.6 0 1 .4 1 1 0 1.3.2 2.5.6 3.6.1.3 0 .7-.2 1z"/></svg>
  <p class="abs foot-text" style="left:573px;top:2841px">CALL US:<br>123 456 7890</p>

  <svg class="abs" style="left:869px;top:2857px" width="22" height="15" viewBox="0 0 22 15" fill="none" stroke="#fff" stroke-width="1.5"><rect x=".75" y=".75" width="20.5" height="13.5"/><polyline points="1,1 11,9 21,1"/><line x1="1" y1="14" x2="8" y2="7"/><line x1="21" y1="14" x2="14" y2="7"/></svg>
  <p class="abs foot-text" style="left:909px;top:2841px">EMAIL US:<br>info@calmnest.example</p>

  <div class="abs legal">2019 ©CALM NEST - All Rights Reserved.</div>
</footer>

</body>
</html>
```